Dental Business Card Design w/logo

Classic, elegant w/a touch of contemporary
Upscale dental facility located in Modesto CA
Specializing in restorative & general dentistry
Providing exceptional customer service to the community
Updates

I prefer script and not bold writing
If you can use the phone; fax and email icons instead of spelling them out, it would be great
No bold colors
Classy and elegant
In the back of the card I would like to see something like this
Your Next Appointment:
Mon     Tue    Wed    Thur (a box next to each of them for marking)
Date:_______________ at_____________ AM    PM  (a box next to them for marking)

Thank you

Target Market(s)

Well established professional

Industry/Entity Type

Dental

Contact Information for Business Card

Velarina Tossudi DMD
4176 Marlow Rd
Suite K7
Modesto, CA 95418

Office: 209-731-5920
Fax: 209-731-8047
Email: tossudidmd@quillmail.example

Requirements
Must have
• Unique classic logo
An easily repeatable design that can be used on letterhead and envelopes
Nice to have
• My initials incorporated into unique design
Should not have
• No cartoons or cheesy themes. This is a practice for the well established and professional individual.

```html
<!DOCTYPE html>
<html lang="en">
<head>
<meta charset="utf-8">
<title>Velarina Tossudi Dentistry – Business Card</title>
<link rel="stylesheet" href="https://fonts.googleapis.com/css2?family=Archivo:wght@700&family=Jost:wght@400;500&display=swap">
<style>
  :root {
    --page: #ffffff;
    --card: #ffffff;
    --card-edge: #2b2b2b;
    --ink: #111111;
    --slate: #5f6b75;
    --leaf: #a6d883;
  }
  * { margin: 0; padding: 0; box-sizing: border-box; }
  html, body {
    width: 1200px; height: 900px; overflow: hidden;
    background: var(--page);
  }
  .card {
    position: absolute;
    left: 118px; top: 170px;
    width: 967px; height: 571px;
    background: var(--card);
    border: 1px solid var(--card-edge);
    overflow: hidden;
  }
  .card__swoosh {
    position: absolute; left: 0; top: 0;
    width: 967px; height: 571px;
  }
  .brand {
    position: absolute;
    left: 40px; top: 70px;
    width: 340px;
    text-align: center;
    font-family: "Jost", sans-serif;
    font-weight: 500;
    color: var(--slate);
  }
  .brand__dot {
    display: block;
    width: 110px; height: 110px;
    margin: 0 auto 36px;
    border-radius: 50%;
    background: var(--leaf);
  }
  .brand__name {
    font-size: 54px;
    line-height: 56px;
    letter-spacing: 1px;
    text-transform: uppercase;
  }
  .brand__tag {
    font-size: 38px;
    line-height: 46px;
    letter-spacing: 0.5px;
    text-transform: uppercase;
  }
  .contact {
    position: absolute;
    right: 29px; top: 118px;
    text-align: right;
    font-family: "Jost", sans-serif;
    color: var(--ink);
  }
  .contact__name {
    font-family: "Archivo", sans-serif;
    font-weight: 700;
    font-size: 49px;
    line-height: 50px;
    letter-spacing: 0.5px;
    text-transform: uppercase;
  }
  .contact__title {
    font-size: 27px;
    line-height: 32px;
    color: var(--slate);
  }
  .contact__address {
    margin-top: 38px;
    font-size: 25px;
    line-height: 33px;
  }
  .contact__lines {
    margin-top: 26px;
    font-size: 28px;
    line-height: 35px;
  }
  .contact__lines .is-email { font-size: 23px; line-height: 32px; }
  .contact__label { color: var(--leaf); font-size: 24px; }
</style>
</head>
<body>
  <div class="card">
    <svg class="card__swoosh" viewBox="0 0 967 571" aria-hidden="true">
      <path d="M398 -2 Q560 285 398 573" fill="none" stroke="var(--leaf)" stroke-width="6"/>
      <path d="M409 -2 Q572 285 409 573" fill="none" stroke="var(--slate)" stroke-width="6"/>
    </svg>

    <div class="brand">
      <span class="brand__dot"></span>
      <div class="brand__name">Velarina</div>
      <div class="brand__name">Tossudi</div>
      <div class="brand__tag">Dentistry</div>
    </div>

    <div class="contact">
      <div class="contact__name">Velarina<br>Tossudi</div>
      <div class="contact__title">DMD</div>
      <div class="contact__address">
        4176 Marlow Rd Suite K7<br>
        Modesto, CA 95418
      </div>
      <div class="contact__lines">
        <div><span class="contact__label">OFFICE:</span> 209-731-5920</div>
        <div><span class="contact__label">FAX:</span> 209-731-8047</div>
        <div class="is-email"><span class="contact__label">EMAIL:</span> tossudidmd@quillmail.example</div>
      </div>
    </div>
  </div>
</body>
</html>
```